Harborline Family Counsel Billboard

We are looking for a billboard design for a Florida divorce law firm. We are unique in the legal field for offering flat fee pricing. Other law firms are expensive, charging hourly rates. We have A LOT of lawyers advertising for personal injury, so we are looking for something fun that will catch the attention and drive home the message that we are an affordable firm to hire for their divorce because we charge a fixed fee. We want people to be directed to steadyratesplit.com

Target Market(s)

Individual seeking a fast and affordable divorce at a fixed fee instead of hourly

Industry/Entity Type

Legal

Requirements
Must have
• Name of firm, logo, steadyratesplit.com, and in small font: Main Office Jacksonville
Should not have
• Promises. Price

```html
<!DOCTYPE html>
<html lang="en">
<head>
<meta charset="utf-8">
<title>Harborline Family Counsel Billboard</title>
<link href="https://fonts.googleapis.com/css2?family=Playfair+Display:wght@600;800&family=Montserrat:wght@400;500;700&display=swap" rel="stylesheet">
<style>
  :root {
    --gold: #a8822e;
    --navy: #12273a;
    --paper: #f3f4f6;
    --paper-shade: #e6e8eb;
    --ring-grey: #7b7f87;
    --photo-top: #66718a;
    --photo-bottom: #8c95a4;
    --stage: #8f9093;
    --white: #ffffff;
  }
  * { margin: 0; padding: 0; box-sizing: border-box; }
  html, body { width: 936px; height: 1200px; overflow: hidden; }
  body { background: var(--stage); position: relative; }

  .billboard {
    position: absolute; left: 28px; top: 380px;
    width: 1512px; height: 756px;
    transform: scale(0.582); transform-origin: top left;
    background: linear-gradient(120deg, var(--paper) 0%, var(--white) 45%, var(--paper-shade) 100%);
    overflow: hidden;
    font-family: "Montserrat", sans-serif;
  }
  .billboard__art { position: absolute; inset: 0; }

  .brand {
    position: absolute; left: 48px; top: 150px; width: 298px;
    text-align: center; color: var(--navy);
    font-family: "Playfair Display", serif; font-weight: 600;
    font-variant: small-caps; font-size: 34px; line-height: 1.02;
  }
  .office {
    position: absolute; left: 477px; top: 157px;
    color: var(--navy); font-size: 22px; line-height: 1.25; letter-spacing: 0.5px;
  }
  .office strong { font-weight: 700; display: block; }

  .headline {
    position: absolute; left: 48px; top: 248px;
    font-family: "Playfair Display", serif; font-weight: 800;
    font-size: 66px; line-height: 1; color: var(--navy);
  }
  .headline .accent { color: var(--gold); }
  .intro {
    position: absolute; left: 48px; top: 390px; width: 720px;
    color: var(--navy); font-size: 19.5px; line-height: 1.4;
  }

  .feature {
    position: absolute; top: 540px; color: var(--white);
    font-size: 21px; line-height: 1.25; font-weight: 500;
  }
  .feature b { font-family: "Playfair Display", serif; font-weight: 800; display: block; }

  .phone {
    position: absolute; left: 108px; top: 658px;
    font-family: "Playfair Display", serif; font-weight: 800;
    font-size: 40px; color: var(--white); letter-spacing: 1px;
  }
  .web {
    position: absolute; left: 458px; top: 670px;
    font-size: 25px; color: var(--white); letter-spacing: 2.5px;
  }
  .web strong { font-weight: 700; }

  .nameplate {
    position: absolute; left: 883px; top: 628px; width: 500px;
    text-align: center;
  }
  .nameplate__firm {
    font-family: "Playfair Display", serif; font-weight: 800;
    font-size: 42px; line-height: 1; color: var(--gold);
  }
  .nameplate__role { font-weight: 700; font-size: 21px; color: var(--navy); margin-top: 4px; }
</style>
</head>
<body>
<main class="billboard">
  <svg class="billboard__art" viewBox="0 0 1512 756" width="1512" height="756">
    <defs>
      <linearGradient id="portraitTone" x1="0" y1="0" x2="0" y2="1">
        <stop offset="0" stop-color="var(--photo-top)"/>
        <stop offset="1" stop-color="var(--photo-bottom)"/>
      </linearGradient>
    </defs>

    <!-- bands -->
    <rect class="band-gold" x="0" y="463" width="1512" height="153" fill="var(--gold)"/>
    <rect class="band-navy" x="0" y="619" width="1512" height="137" fill="var(--navy)"/>

    <!-- ribbon ends -->
    <polygon class="ribbon" points="805,532 895,532 925,615 805,615 835,573" fill="var(--white)"/>
    <polygon class="ribbon" points="1415,532 1465,532 1435,573 1465,615 1345,615" fill="var(--white)"/>

    <!-- portrait frame -->
    <path class="arc-gold" d="M836,463 A318,318 0 1 1 1442,273" fill="none" stroke="var(--gold)" stroke-width="12"/>
    <path class="arc-navy" d="M1223,27 A340,340 0 0 1 1354,615" fill="none" stroke="var(--navy)" stroke-width="9"/>
    <path class="arc-navy-thin" d="M865,511 A312,312 0 0 0 1081,662" fill="none" stroke="var(--navy)" stroke-width="4"/>
    <circle class="ring" cx="1135" cy="355" r="299" fill="var(--white)" stroke="var(--ring-grey)" stroke-width="8"/>
    <circle class="portrait" cx="1135" cy="355" r="290" fill="url(#portraitTone)" role="img" aria-label="Portrait photo of the attorney in a dark suit and gold tie"/>

    <!-- nameplate -->
    <polygon class="nameplate-shape" points="883,619 1383,619 1310,707 955,707" fill="var(--white)"/>

    <!-- brand mark area -->
    <circle class="brand-dot" cx="197" cy="95" r="44" fill="var(--navy)"/>
    <line x1="383" y1="168" x2="383" y2="200" stroke="var(--navy)" stroke-width="3"/>
    <circle cx="440" cy="184" r="23" fill="var(--gold)"/>
    <path d="M440,196 C432,186 431,182 431,178 A9,9 0 0 1 449,178 C449,182 448,186 440,196 Z" fill="none" stroke="var(--white)" stroke-width="2.2"/>
    <circle cx="440" cy="178" r="3" fill="none" stroke="var(--white)" stroke-width="2"/>

    <!-- feature icons -->
    <g class="feature-icon" transform="translate(71,509)">
      <circle r="23" fill="var(--navy)"/>
      <circle r="12" fill="none" stroke="var(--white)" stroke-width="2"/>
      <path d="M0,-7 V0 L5,4" fill="none" stroke="var(--white)" stroke-width="2"/>
    </g>
    <g class="feature-icon" transform="translate(256,509)">
      <circle r="23" fill="var(--navy)"/>
      <path d="M0,-12 V11 M-7,11 H7 M-11,-7 H11 M-11,-7 L-15,3 H-7 Z M11,-7 L7,3 H15 Z" fill="none" stroke="var(--white)" stroke-width="2" stroke-linejoin="round"/>
    </g>
    <g class="feature-icon" transform="translate(482,509)">
      <circle r="23" fill="var(--navy)"/>
      <path d="M-9,0 L-3,6 L10,-7" fill="none" stroke="var(--white)" stroke-width="2.6" stroke-linecap="round"/>
    </g>
    <g class="feature-icon" transform="translate(659,509)">
      <circle r="23" fill="var(--navy)"/>
      <path d="M0,-12 V11 M-7,11 H7 M-11,-7 H11 M-11,-7 L-15,3 H-7 Z M11,-7 L7,3 H15 Z" fill="none" stroke="var(--white)" stroke-width="2" stroke-linejoin="round"/>
    </g>
    <g stroke="var(--white)" stroke-width="2.5">
      <line x1="202" y1="487" x2="202" y2="592"/>
      <line x1="428" y1="487" x2="428" y2="592"/>
      <line x1="605" y1="487" x2="605" y2="592"/>
    </g>

    <!-- contact row -->
    <circle cx="71" cy="685" r="23" fill="var(--gold)"/>
    <path d="M63,676 C61,688 70,696 80,694 L81,689 L76,686 L73,689 C69,688 67,685 66,682 L69,679 L67,674 Z" fill="none" stroke="var(--white)" stroke-width="2" stroke-linejoin="round"/>
    <line x1="383" y1="668" x2="383" y2="702" stroke="var(--gold)" stroke-width="3"/>
    <rect class="web-pill" x="408" y="664" width="437" height="43" rx="21.5" fill="var(--gold)"/>
    <g fill="none" stroke="var(--white)" stroke-width="2">
      <circle cx="431" cy="685" r="12"/>
      <ellipse cx="431" cy="685" rx="5" ry="12"/>
      <line x1="419" y1="685" x2="443" y2="685"/>
    </g>
  </svg>

  <div class="brand">Harborline<br>Family Counsel</div>
  <div class="office">Main Office<strong>Jacksonville</strong></div>

  <h1 class="headline">
    <span class="accent">Are You In</span> Need <span class="accent">Of</span><br>
    <span class="accent">A</span> Divorce Attorney <span class="accent">?</span>
  </h1>
  <p class="intro">Serving all of florida-Dedicated to protecting your rights. We can help you gain the freedom and peace of mind your deserve.</p>

  <div class="feature" style="left:48px"><b>24/7</b>Availability</div>
  <div class="feature" style="left:233px"><b>Flat Free</b>for most cases</div>
  <div class="feature" style="left:459px"><b>100%</b>Dedicated</div>
  <div class="feature" style="left:636px"><b>20 Years</b>in Practice</div>

  <div class="phone">855-300-0142</div>
  <div class="web">www.<strong>steadyratesplit</strong>.com</div>

  <div class="nameplate">
    <div class="nameplate__firm">Halden &amp; Pryce</div>
    <div class="nameplate__role">Divorce Attorneys</div>
  </div>
</main>
</body>
</html>
```